Tradlo - Forex Signal Services Moments Matter Most. Reshape your path.

I need an attractive eye catching web design that is azure friendly. I currently have a web programmer working on the backend of my website. Now I need a professional design to attract and retain customers. This site needs to be mobile friendly.

Tradlo is a highly reputable, trustworthy and professional site that offers forex signals to traders in all parts of the globe. With accurate and reliable forex signals, traders can not only make money but also boost their profits.

At Tradlo, we want our clients to have complete faith on us and our services! We also do not want our users to lead a simple and monotonous life. Instead our goal is to help them create an extra source of steady income. However, this is possible only when our clients resolve to change their lives for the better. They need to change their mindset and most importantly develop a positive frame of mind. That’s exactly why at Tradlo, we provide our clients with innumerable personal development tools and resources that’ll aid them in changing all the aspects of their lives. We want our traders to feel inspired and educate them in the right way!

Colors are flexible.

I do like the simplicity of www.brightmarkvo.example.
I do want a design more professional in appearance and not everything on page one.

I have not been able to decide on a logo. There is one of lower quality as I have not paid for it yet but I will if you decide it's the best for my business I will. Or should one feel that they have a better idea for a logo, I will pay for it if i like it.

I have included some of the content of my site so you can get a feel for where I am coming from.
(Please note that this content is still in the editing process)
Updates

Project Deadline Extended Reason: My content was not complete nor finalization of the final logo. We will allow a few more days for designers to modify the website.Thank you for your patience and understanding. Added Tuesday, January 24, 2017

Target Market(s)

I work with Forex Traders, Investors wanting to control their own portfolios, and remote nomads/mellienials

Coding

Coded - Design and coding required

Number of Pages Required

5+ page

Requirements
Must have
• I must have a professional clean look. I want the site to be interactive and eye catching. I want my audience hooked within seconds of opening it. It has to have all important information first. Photos must be legit and not spammy. I work as a representative in the financial market. I want my site to reflect that I stand by my product and reputation means everything to me. This site has to be engaging.
• Sorry, I should have included this earlier of what I will all need on this site.
• I'll have about Tradlo (my company, what we stand for, who we work with, my strategy, etc....
• about me (why i started this company, who I am)
• Performance (graphs and recent posts of signals)
• Membership (how to sign up)
• Terms of service/legal/disclaimers
• FAQS
• Personal Development Resources
• Forex Education Resources
Nice to have
• Quick links to bounce around the site faster.
Should not have
• I do not want over the top white collar conservative.

```html
<!DOCTYPE html>
<html lang="en">
<head>
<meta charset="utf-8">
<title>Tradlo - Forex Signal Services</title>
<link href="https://fonts.googleapis.com/css2?family=Lato:wght@300;400;700;900&family=Oswald:wght@400;600&display=swap" rel="stylesheet">
<style>
:root{
  --orange:#e2694a;
  --green:#6db66b;
  --blue:#2f86e0;
  --blue-deep:#1f6fd0;
  --navy:#0d2a55;
  --dark:#14171d;
  --ink:#2c2f36;
  --muted:#5b606a;
  --white:#ffffff;
  --line:#c9ced6;
}
*{box-sizing:border-box;margin:0;padding:0}
html,body{width:1200px;height:2635px;overflow:hidden}
body{position:relative;font-family:"Lato",sans-serif;color:var(--ink);background:var(--white)}
.abs{position:absolute}

/* header */
.topbar-white{left:357px;top:0;width:603px;height:67px;background:var(--white)}
.brand{left:225px;top:0;width:132px;height:67px;background:#000;display:flex;align-items:center;justify-content:center;gap:8px}
.brand-dot{width:14px;height:14px;border-radius:50%;background:var(--blue)}
.brand-name{font-weight:900;font-size:22px;color:var(--white)}
.appointment{left:367px;top:5px;font-size:9px;color:var(--muted)}
.socials-top{left:864px;top:6px;display:flex;gap:8px}
.socials-top span{width:14px;height:14px;background:var(--blue-deep);display:block}
.socials-top span+span{background:#8a909a;width:10px;height:10px;margin-top:2px;border-radius:50%}
.nav{left:452px;top:44px;display:flex;gap:15px;align-items:center;font-size:8.5px;font-weight:700;color:#222;text-transform:uppercase;white-space:nowrap}
.nav .active{color:var(--blue)}
.nav .search{width:9px;height:9px;border:1.5px solid #666;border-radius:50%;margin-left:2px}

/* hero */
.hero{left:0;top:0;width:1200px;height:618px;background:linear-gradient(160deg,#0b2c62 0%,#1a5fae 40%,#2f86e0 60%,#0f3a78 100%)}
.hero-band{left:0;top:233px;width:1200px;height:145px;background:rgba(20,60,120,.55)}
.hero-title{left:0;top:240px;width:1200px;text-align:center;font-family:"Oswald",sans-serif;font-weight:600;font-size:57px;letter-spacing:5px;color:var(--white);line-height:1}
.hero-sub{left:0;top:296px;width:1200px;text-align:center;font-family:"Oswald",sans-serif;font-size:19px;letter-spacing:22px;color:var(--white);line-height:1}
.hero-text{left:395px;top:316px;width:410px;text-align:center;font-size:13px;line-height:19px;color:#e6eefb}
.arrow{top:276px;width:62px;height:58px;background:rgba(255,255,255,.75);display:flex;align-items:center;justify-content:center}
.arrow-left{left:0}.arrow-right{left:1138px}

/* features */
.feature{top:513px;width:256px;height:186px;color:var(--white);text-align:center;padding:20px 16px 0}
.feature-orange{left:216px;background:var(--orange)}
.feature-green{left:472px;background:var(--green)}
.feature-blue{left:728px;background:var(--blue)}
.feature h3{font-weight:400;font-size:17px;letter-spacing:1px;margin-top:10px;text-transform:uppercase;white-space:nowrap}
.feature p{font-size:9.5px;font-weight:700;line-height:13px;margin-top:8px}

/* welcome */
.welcome-bg{left:0;top:618px;width:1200px;height:515px;background:linear-gradient(180deg,#f4f6f9 0%,#e6ebf1 60%,#dfe6ee 100%)}
.welcome-title{left:0;top:728px;width:1200px;text-align:center;font-weight:400;font-size:34px;letter-spacing:9px;color:var(--blue)}
.welcome-tag{left:0;top:776px;width:1200px;text-align:center;font-size:18px;letter-spacing:2px;color:var(--orange);text-transform:uppercase}
.welcome-tag2{left:0;top:799px;width:1200px;text-align:center;font-size:18px;letter-spacing:2px;color:var(--blue);text-transform:uppercase}
.welcome-p{left:258px;width:684px;text-align:center;font-size:12.5px;line-height:15px;letter-spacing:.6px;color:#333}
.welcome-h{left:0;top:978px;width:1200px;text-align:center;font-size:16px;font-weight:700;letter-spacing:2px;color:var(--blue);text-transform:uppercase}

/* membership */
.plans-bg{left:0;top:1133px;width:1200px;height:461px;background:linear-gradient(180deg,#2a7fde 0%,#2279d8 55%,#1d6ecb 100%)}
.plans-title{left:0;top:1158px;width:1200px;text-align:center;font-weight:300;font-size:46px;letter-spacing:8px;color:var(--white)}
.plans-p{left:262px;width:676px;text-align:center;font-size:12px;line-height:14.5px;letter-spacing:.3px;color:#e8f0fc}
.card{top:1406px;width:227px;height:263px;background:var(--white);box-shadow:0 2px 6px rgba(0,0,0,.25);text-align:center}
.card-price{height:40px;background:var(--orange);color:var(--white);font-size:21px;letter-spacing:3px;line-height:40px}
.card-term{height:30px;background:var(--green);color:var(--white);font-size:14px;letter-spacing:4px;line-height:30px}
.card-note{font-size:15px;color:#8a8f98;line-height:18px;margin-top:15px}
.card-btn{display:inline-block;margin-top:14px;width:112px;height:30px;line-height:30px;background:var(--blue-deep);color:var(--white);font-size:11px;font-weight:700;letter-spacing:1px}
.pay-name{font-size:17px;font-weight:900;color:var(--navy);margin-top:16px}
.pay-buy{width:72px;height:13px;margin:3px auto 0;background:#f4b538;border-radius:7px;font-size:8px;font-weight:700;color:var(--navy);line-height:13px}
.pay-cards{display:flex;gap:2px;justify-content:center;margin-top:4px}
.pay-cards span{width:11px;height:7px;background:#9aa3b0}

/* faq */
.faq-bg{left:0;top:1594px;width:1200px;height:520px;background:linear-gradient(135deg,#dfe9f3 0%,#eef3f8 45%,#d5e4f1 100%)}
.faq-title{left:0;top:1702px;width:1200px;text-align:center;font-weight:400;font-size:32px;letter-spacing:18px;color:var(--blue)}
.faq-item{width:342px;height:34px;border-bottom:1px solid #8b919b;display:flex;align-items:center;gap:16px;font-size:10.5px;font-weight:700;color:#222;white-space:nowrap}
.faq-icon{width:12px;height:12px;background:#222;position:relative;flex:none}
.faq-icon::before,.faq-icon::after{content:"";position:absolute;background:var(--white)}
.faq-icon::before{left:2px;top:5px;width:8px;height:2px}
.faq-icon::after{left:5px;top:2px;width:2px;height:8px}
.faq-open{left:234px;top:1784px;width:326px}
.faq-open-q{display:flex;align-items:center;gap:10px;font-size:10.5px;color:var(--blue)}
.faq-open-q .x{width:14px;height:14px;background:var(--blue);color:var(--white);font-size:11px;line-height:14px;text-align:center;flex:none}
.faq-open p{font-size:8px;line-height:10.5px;color:#333;margin-top:12px}

/* contact */
.contact-bg{left:0;top:2114px;width:1200px;height:478px;background:linear-gradient(160deg,#1e2531 0%,#11151b 55%,#1a2029 100%)}
.contact-title{left:0;top:2166px;width:1200px;text-align:center;font-weight:700;font-size:27px;letter-spacing:6px;color:var(--white)}
.contact-rule{left:570px;top:2207px;width:60px;height:2px;background:var(--blue)}
.contact-intro{left:239px;top:2250px;width:220px;font-size:11px;line-height:14px;color:#dde2ea}
.contact-alt{left:239px;top:2308px;font-size:11px;color:#dde2ea}
.contact-phone{left:239px;top:2320px;font-size:28px;font-weight:700;letter-spacing:1px;color:var(--blue)}
.stay{left:239px;top:2380px;font-size:14px;font-weight:700;letter-spacing:3px;color:var(--white)}
.social{top:2407px;width:49px;height:49px;border-radius:50%}
.field{height:31px;border-top:2px solid var(--blue);background:rgba(40,48,60,.85);font-size:10px;letter-spacing:2px;color:#aeb6c2;padding:8px 14px}
.message{left:490px;top:2379px;width:475px;height:93px}
.remote{left:234px;top:2500px;width:351px;height:36px;border:1px solid var(--blue);display:flex;align-items:center}
.remote-tag{width:96px;height:100%;flex:none;background:var(--blue-deep);color:var(--white);font-size:10px;font-weight:700;display:flex;align-items:center;justify-content:center;gap:5px}
.remote-tag span{width:10px;height:10px;border-radius:50%;background:var(--white)}
.remote p{font-size:8.5px;line-height:11px;color:#dde2ea;padding:0 8px}
.send{left:859px;top:2509px;width:106px;height:27px;background:var(--blue-deep);color:var(--white);font-size:10px;letter-spacing:2px;text-align:center;line-height:27px}
.foot-link{font-size:9px;letter-spacing:1px;color:#dde2ea;line-height:11px;text-transform:uppercase;white-space:nowrap}
.bottom{left:0;top:2592px;width:1200px;height:43px;background:var(--blue);color:var(--white)}
.bottom p{position:absolute;left:240px;top:12px;font-size:10px;letter-spacing:1px}
.bottom .top-link{left:883px;top:16px}
</style>
</head>
<body>

<!-- hero -->
<div class="abs hero" role="img" aria-label="Stock market ticker numbers and chart lines on a blue screen"></div>
<div class="abs hero-band"></div>

<!-- header -->
<div class="abs topbar-white"></div>
<div class="abs brand"><span class="brand-dot"></span><span class="brand-name">Tradlo</span></div>
<div class="abs appointment">Make an Appointment | Call : 555-014-2270</div>
<div class="abs socials-top"><span></span><span></span><span></span><span></span></div>
<nav class="abs nav">
  <span class="active">Home</span><span>About Us</span><span>Membership Plans</span><span>Performance</span><span>FAQ</span><span>Forex Resources</span><span>Contact</span><span class="search"></span>
</nav>

<h1 class="abs hero-title">FOREX SIGNAL</h1>
<div class="abs hero-sub">SERVICES</div>
<p class="abs hero-text">Tradlo.com works with both day as well as intraday traders. We only hold a maximum of one position at any given point in time. Once we've placed an order we do not move SL or TP targets.</p>
<div class="abs arrow arrow-left"><svg width="14" height="20" viewBox="0 0 14 20"><path d="M11 2 3 10l8 8" fill="none" stroke="#222" stroke-width="2.5"/></svg></div>
<div class="abs arrow arrow-right"><svg width="14" height="20" viewBox="0 0 14 20"><path d="M3 2l8 8-8 8" fill="none" stroke="#222" stroke-width="2.5"/></svg></div>

<!-- welcome background -->
<div class="abs welcome-bg" role="img" aria-label="Faded photo of a hand with a pen over printed financial charts"></div>

<!-- features -->
<div class="abs feature feature-orange">
  <svg width="44" height="40" viewBox="0 0 44 40"><circle cx="16" cy="22" r="10" fill="none" stroke="#fff" stroke-width="6" stroke-dasharray="4 3"/><circle cx="16" cy="22" r="4" fill="#fff"/><circle cx="33" cy="10" r="6" fill="none" stroke="#fff" stroke-width="4" stroke-dasharray="3 2"/></svg>
  <h3>The Tradlo Advantage</h3>
  <p>Delivering high-probability forex signals to help you beat the market. Accurate and reliable forex signals to take your trading</p>
</div>
<div class="abs feature feature-green">
  <svg width="44" height="40" viewBox="0 0 44 40"><rect x="4" y="28" width="6" height="10" fill="#fff"/><rect x="14" y="22" width="6" height="16" fill="#fff"/><rect x="24" y="16" width="6" height="22" fill="#fff"/><path d="M4 20 18 10l8 5L40 4" fill="none" stroke="#fff" stroke-width="3"/><path d="M32 3h9v9" fill="none" stroke="#fff" stroke-width="3"/></svg>
  <h3>Tradlo Philosophy</h3>
  <p>Capital protection is the key to consistent profitability and equity growth flexibility and taking advantage of opportunities when they arise.</p>
</div>
<div class="abs feature feature-blue">
  <svg width="44" height="40" viewBox="0 0 44 40"><path d="M18 6h16v30H18" fill="none" stroke="#fff" stroke-width="4"/><path d="M6 21h20M19 14l7 7-7 7" fill="none" stroke="#fff" stroke-width="4"/></svg>
  <h3>Tradlo Free Trial</h3>
  <p>Free forex signals for 30 days. trading signals to help you beat the forex market.</p>
</div>

<!-- welcome -->
<h2 class="abs welcome-title">Welcome to Tradlo</h2>
<div class="abs welcome-tag">Moments Matter Most. Reshape your path</div>
<div class="abs welcome-tag2">Forex Signal Services</div>
<p class="abs welcome-p" style="top:840px">We use proven strategies to help traders in succeeding in the forex market. Our forex experts provide high-probability, professional and consistent forex signals and charts that help traders in maximizing their profits and eliminating losses.</p>
<p class="abs welcome-p" style="top:902px">We use proven strategies to help traders in succeeding in the forex market. Our forex experts provide high-probability, professional and consistent forex signals and charts that help traders in maximizing their profits and eliminating losses. Try our free Currency Education service to find out what differentiates us from our competitors and how we can aid you in becoming a professional trader!</p>
<h3 class="abs welcome-h">What is your trading philosophy and style?</h3>
<p class="abs welcome-p" style="top:1013px">We follow naked forex trading techniques including price action, immediate trend and personalized mathematical formulas. Our success stems from our strict enforcement of discipline, patience, attitude, economics and timing to help our traders maximize their gains from forex trading. Obviously we do not always win, but our winning trades exceed those that are not and our take profit target is always bigger than our stop loss. We look at multiple time frames to qualify setups that define our trading edge. We pay close to the London market and our entries are often based off of the 1-hour chart.</p>

<!-- membership -->
<div class="abs plans-bg" role="img" aria-label="Blue tinted photo of a trading desk"></div>
<h2 class="abs plans-title">Membership Plans</h2>
<p class="abs plans-p" style="top:1215px">Disclaimer Trading foreign exchange ("Forex") on margin carries a high level of risk, and may not be suitable for all investors. Before deciding to trade Forex you should carefully consider your investment objectives, level of experience, and only trade with the money you are prepared to lose. The possibility exists that you could sustain a loss in excess of all of your deposited funds and therefore you should not speculate with capital that you cannot afford to lose. You should be aware of all the risks associated with foreign exchange.</p>
<p class="abs plans-p" style="top:1309px">Clients must be at least 18 years old to use the services of TRADLO. You acknowledge that past performance is not an indicator of future returns and that references to performance on this Site are provided as historical benchmarks only. TRADLO does not take responsibility for loss incurred as a result of our trading signals. By signing up as a member you acknowledge that we are not providing financial advice and that you are making the decision to use our trades on your own account. All information provided by TRADLO, in any form, is for educational purposes only.</p>

<div class="abs card" style="left:244px">
  <div class="card-price">$ 58 USD</div><div class="card-term">1 MONTH</div>
  <p class="card-note">Click here to<br>sign up for 1 month</p>
  <span class="card-btn">ORDER NOW</span>
  <div class="pay-name">PayLink</div><div class="pay-buy">Buy Now</div>
  <div class="pay-cards"><span></span><span></span><span></span><span></span><span></span></div>
</div>
<div class="abs card" style="left:485px">
  <div class="card-price">$ 145 USD</div><div class="card-term">3 MONTH</div>
  <p class="card-note">Click here to<br>sign up for 1 month</p>
  <span class="card-btn">ORDER NOW</span>
  <div class="pay-name">PayLink</div><div class="pay-buy">Buy Now</div>
  <div class="pay-cards"><span></span><span></span><span></span><span></span><span></span></div>
</div>
<div class="abs card" style="left:726px">
  <div class="card-price">$ 450 USD</div><div class="card-term">12 MONTH</div>
  <p class="card-note">Click here to<br>sign up for 1 month</p>
  <span class="card-btn">ORDER NOW</span>
  <div class="pay-name">PayLink</div><div class="pay-buy">Buy Now</div>
  <div class="pay-cards"><span></span><span></span><span></span><span></span><span></span></div>
</div>

<!-- faq -->
<div class="abs faq-bg" role="img" aria-label="Light blue photo of a hand holding a phone with glowing forex graphics" style="z-index:-1"></div>
<h2 class="abs faq-title">FAQ</h2>
<div class="abs faq-open">
  <div class="faq-open-q"><span class="x">✕</span>How many pips can I make per month following your signals?</div>
  <p>Our view is simple. Trading is a business and not for the faint of heart. We strive to achieve 150-250 quality pips a month. More importantly, we care more about protecting our capital and keeping drawdowns small than chasing big numbers every week. We stick to our strategy and rules. Drawdowns are a fact of trading life and our aim is to keep them as small as we can, even if that means giving up some extra pips along the way.</p>
</div>
<div class="abs faq-item" style="left:234px;top:1946px"><span class="faq-icon"></span>Can I follow your signals and have a full time job?</div>
<div class="abs faq-item" style="left:234px;top:1995px"><span class="faq-icon"></span>How will I receive my signals?</div>
<div class="abs faq-item" style="left:234px;top:2046px"><span class="faq-icon"></span>What happens after my trial period access?</div>
<div class="abs faq-item" style="left:622px;top:1799px"><span class="faq-icon"></span>How Will FOREX Signals Help You?</div>
<div class="abs faq-item" style="left:622px;top:1848px"><span class="faq-icon"></span>What we are not or should I say what we are?</div>
<div class="abs faq-item" style="left:622px;top:1897px"><span class="faq-icon"></span>How many pips can I make per month following your signals?</div>
<div class="abs faq-item" style="left:622px;top:1946px"><span class="faq-icon"></span>Don't need special requirements to earn money from my system?</div>
<div class="abs faq-item" style="left:622px;top:1995px"><span class="faq-icon"></span>Who do we serve?</div>
<div class="abs faq-item" style="left:622px;top:2046px"><span class="faq-icon"></span>How many pips can I make per month following your signals?</div>

<!-- contact -->
<div class="abs contact-bg" role="img" aria-label="Dark photo of a hand drawing a business chart"></div>
<h2 class="abs contact-title">CONTACT US</h2>
<div class="abs contact-rule"></div>
<p class="abs contact-intro">If you would like to get in contact with us, please fill in the form and we will get back to you as soon as we can.</p>
<p class="abs contact-alt">Alternatively you can call us on</p>
<div class="abs contact-phone">0800 555 0142</div>
<div class="abs stay">STAY CONNECTED</div>
<div class="abs social" style="left:234px;background:var(--orange)" aria-label="Social network one"></div>
<div class="abs social" style="left:287px;background:#3b5a9a" aria-label="Social network two"></div>
<div class="abs social" style="left:340px;background:#1d7fb3" aria-label="Social network three"></div>
<div class="abs social" style="left:393px;background:#3ba5e6" aria-label="Social network four"></div>

<div class="abs field" style="left:490px;top:2254px;width:222px">Name</div>
<div class="abs field" style="left:740px;top:2254px;width:225px">Email</div>
<div class="abs field" style="left:490px;top:2316px;width:222px">Telephone</div>
<div class="abs field" style="left:740px;top:2316px;width:225px">Subject</div>
<div class="abs field message">Message</div>

<div class="abs remote"><div class="remote-tag"><span></span>RemoteDesk</div><p>If requested by our staff to do so, please click on this link to start our <b>Remote Assistance Software</b>.</p></div>
<div class="abs send">SEND</div>

<nav class="footer-nav">
  <span class="abs foot-link" style="left:369px;top:2557px">Home</span>
  <span class="abs foot-link" style="left:443px;top:2557px">About Us</span>
  <span class="abs foot-link" style="left:538px;top:2557px">Membership Plans</span>
  <span class="abs foot-link" style="left:689px;top:2557px">Performance</span>
  <span class="abs foot-link" style="left:810px;top:2557px">FAQ</span>
  <span class="abs foot-link" style="left:337px;top:2569px">Forex Resources</span>
  <span class="abs foot-link" style="left:480px;top:2569px">Why Us?</span>
  <span class="abs foot-link" style="left:573px;top:2569px">Our Strategy</span>
  <span class="abs foot-link" style="left:694px;top:2569px">Investors</span>
  <span class="abs foot-link" style="left:796px;top:2569px">Disclaimer</span>
</nav>

<footer class="abs bottom">
  <p>2017 © TRADLO ALL RIGHTS RESERVED.</p>
  <p class="top-link">BACK TO TOP &nbsp;⌃</p>
</footer>

</body>
</html>
```